Healthcare technology firm needs business card layout. Logo provided.

We need a business card design for a new healthcare technology company called BelnaVix.net. The logo is already done so that will be used in the design. We assist patients and their families manage their personal health finances. Our initial product is our web site membership that includes educational content on your health benefits, tools, and downloadable forms.

We would like to see designs that use our existing logo or extend the logo in a creative way. Should be very consumer friendly.

Industry/Entity Type

Healthcare

```html
<!DOCTYPE html>
<html lang="en">
<head>
<meta charset="utf-8">
<title>BelnaVix Business Card</title>
<link rel="stylesheet" href="https://fonts.googleapis.com/css2?family=Arimo:wght@400;700&family=Open+Sans:wght@400;600&display=swap">
<style>
  :root {
    --stage: #0b0b0b;
    --paper: #ffffff;
    --brand-blue: #1d5a9c;
    --brand-green: #3aa845;
    --teal: #1f8ea6;
    --band-dark: #123f6e;
    --band-light: #2a7fb0;
    --ink-name: #1c4f8c;
  }
  * { box-sizing: border-box; margin: 0; padding: 0; }
  html, body { width: 1200px; height: 900px; overflow: hidden; background: var(--stage); }
  .stage { position: relative; width: 1200px; height: 900px; }
  .card {
    position: absolute; left: 280px; width: 640px; height: 366px;
    background: var(--paper); border-radius: 34px; overflow: hidden;
  }
  .card--front { top: 60px; }
  .card--back { top: 474px; }
  .card__band { position: absolute; left: 0; top: 0; width: 640px; height: 366px; }
  .wordmark {
    position: absolute; left: 0; right: 0; text-align: center;
    font-family: "Open Sans", sans-serif; font-weight: 600; color: var(--brand-blue);
    letter-spacing: 1px;
  }
  .wordmark::after {
    content: ""; display: inline-block; width: 14px; height: 14px; border-radius: 50%;
    background: var(--brand-blue); margin-left: 8px; vertical-align: middle;
  }
  .card--front .wordmark { top: 26px; font-size: 52px; }
  .card--back .wordmark { top: 92px; font-size: 62px; }
  .contact { position: absolute; left: 34px; top: 150px; font-family: "Arimo", sans-serif; color: var(--teal); font-size: 17px; }
  .contact__row { display: flex; align-items: flex-start; gap: 10px; margin-bottom: 8px; }
  .contact__icon { flex: none; width: 26px; height: 26px; }
  .contact__text { line-height: 21px; padding-top: 2px; }
  .person { position: absolute; left: 380px; top: 150px; font-family: "Arimo", sans-serif; }
  .person__name { font-size: 27px; font-weight: 700; color: var(--ink-name); }
  .person__title { font-size: 14px; font-weight: 700; color: var(--brand-green); margin-top: 4px; }
  .tagline {
    position: absolute; left: 0; right: 0; top: 300px; text-align: center;
    font-family: "Open Sans", sans-serif; font-size: 20px; color: #ffffff; letter-spacing: 0.5px;
    transform: rotate(-4deg);
  }
  .web { position: absolute; left: 0; right: 0; top: 192px; text-align: center;
    font-family: "Open Sans", sans-serif; font-weight: 600; font-size: 26px; color: var(--teal); letter-spacing: 1px; }
</style>
</head>
<body>
<main class="stage">
  <section class="card card--front">
    <svg class="card__band" viewBox="0 0 640 366" aria-hidden="true">
      <defs>
        <linearGradient id="bandFront" x1="0" y1="0" x2="0" y2="1">
          <stop offset="0" stop-color="var(--band-light)"/>
          <stop offset="1" stop-color="var(--band-dark)"/>
        </linearGradient>
      </defs>
      <path d="M0 296 Q320 262 640 232 L640 366 L0 366 Z" fill="url(#bandFront)"/>
      <path d="M0 296 Q320 262 640 232" fill="none" stroke="var(--brand-green)" stroke-width="6"/>
    </svg>
    <div class="wordmark">BelnaVix</div>
    <div class="contact">
      <div class="contact__row">
        <svg class="contact__icon" viewBox="0 0 26 26" aria-hidden="true"><circle cx="13" cy="13" r="11.5" fill="none" stroke="var(--teal)" stroke-width="2"/><path d="M7 13 L13 7.5 L19 13 M9 12 V18 H17 V12" fill="none" stroke="var(--brand-green)" stroke-width="2"/></svg>
        <div class="contact__text">Maple Ridge Harbor Point<br>Elm Valley Northgate</div>
      </div>
      <div class="contact__row">
        <svg class="contact__icon" viewBox="0 0 26 26" aria-hidden="true"><circle cx="13" cy="13" r="11.5" fill="none" stroke="var(--teal)" stroke-width="2"/><rect x="9" y="6" width="8" height="14" rx="1.5" fill="var(--brand-green)"/><rect x="10.5" y="8" width="5" height="5" fill="#fff"/></svg>
        <div class="contact__text">555-014-2290</div>
      </div>
      <div class="contact__row">
        <svg class="contact__icon" viewBox="0 0 26 26" aria-hidden="true"><circle cx="13" cy="13" r="11.5" fill="none" stroke="var(--teal)" stroke-width="2"/><circle cx="13" cy="13" r="6.5" fill="none" stroke="var(--brand-green)" stroke-width="1.6"/><path d="M6.5 13 H19.5 M13 6.5 V19.5" stroke="var(--brand-green)" stroke-width="1.4"/></svg>
        <div class="contact__text">www.belnavix.net</div>
      </div>
    </div>
    <div class="person">
      <div class="person__name">Marian T. Cole</div>
      <div class="person__title">CEO</div>
    </div>
    <div class="tagline">Guiding Your Care Costs Clearly</div>
  </section>

  <section class="card card--back">
    <svg class="card__band" viewBox="0 0 640 366" aria-hidden="true">
      <defs>
        <linearGradient id="bandBack" x1="0" y1="0" x2="0" y2="1">
          <stop offset="0" stop-color="var(--band-light)"/>
          <stop offset="1" stop-color="var(--band-dark)"/>
        </linearGradient>
      </defs>
      <path d="M0 316 Q320 282 640 262 L640 366 L0 366 Z" fill="url(#bandBack)"/>
      <path d="M0 316 Q320 282 640 262" fill="none" stroke="var(--brand-green)" stroke-width="6"/>
    </svg>
    <div class="wordmark">BelnaVix</div>
    <div class="web">www.belnavix.net</div>
  </section>
</main>
</body>
</html>
```